Card Design for my dog training business Brightpaw Obedience

Need a business card design for my dog training business with my new logo. Want the card to come off professional yet fun. Want it to be very eye catchy as well. I normally have these at vet clinics, pet stores, and groomers. so need it to look better than my competitors.
Target Market(s)
dog owners
Industry/Entity Type
Dog Training
Contact Information for Business Card
needs logo, my name and info
Font styles to use
Serif
Colors
0255a3
ffffff
ec1f27
000000
333333
fbfbfb
Requirements
Must have
- Brightpaw Obedience
- Felix Orland
- 415 903 2276
- info@brightpawobedience.example
- www.brightpawobedience.example

```html
<!DOCTYPE html>
<html lang="en">
<head>
<meta charset="utf-8">
<title>Brightpaw Obedience – Business Card</title>
<link rel="stylesheet" href="https://fonts.googleapis.com/css2?family=Montserrat:wght@400;600;700&family=Libre+Baskerville:ital@1&display=swap">
<style>
  :root {
    --blue: #0255a3;
    --red: #ec1f27;
    --black: #000000;
    --ink: #333333;
    --white: #ffffff;
    --paper: #fbfbfb;
    --backdrop: #ececec;
    --card-dark: #2f2f2f;
    --emboss: #262626;
  }
  * { margin: 0; padding: 0; box-sizing: border-box; }
  html, body { width: 1200px; height: 1200px; overflow: hidden; }
  body {
    background: var(--backdrop);
    display: flex;
    align-items: center;
    justify-content: center;
    gap: 80px;
    font-family: "Montserrat", Arial, sans-serif;
  }
  .card {
    width: 380px;
    height: 665px;
    border-radius: 4px;
    box-shadow: 0 6px 18px rgba(0,0,0,0.12);
    display: flex;
    flex-direction: column;
    align-items: center;
  }
  .card--back {
    background: var(--card-dark);
    justify-content: center;
  }
  .card--back .brand-mark {
    color: var(--emboss);
    font-size: 30px;
    font-weight: 700;
    text-align: center;
    line-height: 1.2;
    text-shadow: none;
  }
  .card--front {
    background: var(--paper);
    padding: 70px 30px 0;
  }
  .brand-mark {
    font-family: "Montserrat", Arial, sans-serif;
    font-weight: 700;
    font-size: 28px;
    line-height: 1.2;
    text-align: center;
    color: var(--blue);
  }
  .brand-block {
    height: 190px;
    display: flex;
    align-items: center;
    justify-content: center;
  }
  .tagline {
    margin-top: 22px;
    font-family: "Libre Baskerville", Georgia, serif;
    font-style: italic;
    font-size: 12.5px;
    color: var(--ink);
    text-align: center;
  }
  .person { margin-top: 58px; text-align: center; }
  .person__name {
    font-weight: 700;
    font-size: 22px;
    color: var(--blue);
  }
  .person__role {
    font-size: 14px;
    color: var(--ink);
    margin-top: 2px;
  }
  .contact-icons {
    margin-top: 16px;
    display: flex;
    gap: 10px;
  }
  .contact-icons svg { width: 14px; height: 14px; }
  .contact-list {
    margin-top: 10px;
    list-style: none;
    text-align: center;
    font-size: 14px;
    line-height: 1.55;
    color: var(--ink);
  }
</style>
</head>
<body>
  <section class="card card--back" aria-label="Card back">
    <div class="brand-mark">Brightpaw<br>Obedience</div>
  </section>

  <section class="card card--front" aria-label="Card front">
    <div class="brand-block">
      <div class="brand-mark">Brightpaw<br>Obedience</div>
    </div>
    <p class="tagline">“Training dogs across Texas one dog at a time.”</p>
    <div class="person">
      <div class="person__name">Felix Orland</div>
      <div class="person__role">Owner</div>
    </div>
    <div class="contact-icons" aria-hidden="true">
      <svg viewBox="0 0 16 16"><path d="M4 1.5 6.5 4.5 5 6.5c1 2 2.5 3.5 4.5 4.5l2-1.5 3 2.5-1.5 2.5C7 14 2 9 1.5 3z" fill="var(--red)"/></svg>
      <svg viewBox="0 0 16 16"><rect x="1.5" y="3.5" width="13" height="9" fill="none" stroke="var(--red)" stroke-width="1.6"/><path d="M1.5 3.5 8 9l6.5-5.5" fill="none" stroke="var(--red)" stroke-width="1.6"/></svg>
      <svg viewBox="0 0 16 16"><circle cx="8" cy="8" r="6.3" fill="none" stroke="var(--red)" stroke-width="1.4"/><ellipse cx="8" cy="8" rx="2.8" ry="6.3" fill="none" stroke="var(--red)" stroke-width="1.2"/><path d="M1.7 8h12.6M2.8 4.8h10.4M2.8 11.2h10.4" stroke="var(--red)" stroke-width="1.1"/></svg>
    </div>
    <ul class="contact-list">
      <li>415 903 2276</li>
      <li>info@brightpawobedience.example</li>
      <li>www.brightpawobedience.example</li>
    </ul>
  </section>
</body>
</html>
```